International Book about Player ethics in stadiums - This book will be presented to players in all

This book will be distributed to players to learn about the mathematical ethics, and the spirit of sport required for the ideal player
It also aims to teach the public the morals of encouragement and some instructions about keeping the playgrounds beautiful
Size : w 15 x 21 H
Title of the book
نجوم على ضفاف الغروب
Author
تاليف / الدكتور ناصر بن عيسى المرزوقي
1440-2018

Target Market(s)

This book will be presented to players in all activities

Colors

Designer to choose colors to be used in the design.

Requirements
Must have
• Selected colors must be related to play, players, activity and vitality.
• To be the attractive design makes the book lovable
• Final design of the file in the front and back should be on files illustrator and Photoshop and accept the opening on the lower versions
•  
Nice to have
• Example:
• Option 1
• stadium image
• The image must be for a mathematical expression
• For example: a player extends his hand to the opponent to help him from the ground or
• Two players from the two teams are hugging - shaking hands
• Option 2
• The picture can be a sports track
• On both sides of the track are the names of sports ethics - fair play - sportsmanship - compassion - clean encouragement - discipline - respect - apology ... etc
Should not have
• Direct images of famous players or people
• In the case of images should be indirect - or possible to be drawings
• Direct photos of famous people or players are not required

```html
<!DOCTYPE html>
<html lang="ar" dir="rtl">
<head>
<meta charset="utf-8">
<title>نجوم على ضفاف الغروب</title>
<link rel="stylesheet" href="https://fonts.googleapis.com/css2?family=Reem+Kufi:wght@500;700&display=swap">
<style>
  :root {
    --paper: #ffffff;
    --title-purple: #93378f;
    --title-teal: #1ba48f;
    --author-ink: #111111;
    --sky-top: #6f6c58;
    --sky-mid: #c9c08a;
    --glow: #fff6c8;
    --stand-amber: #8a5a22;
    --stand-dark: #2a2620;
    --pitch: #2f6a1f;
    --pitch-dark: #1f4a14;
    --crop: #333333;
    --publisher: #fff1d0;
    --publisher-mark: #d9792a;
  }
  html, body {
    margin: 0;
    padding: 0;
    width: 1200px;
    height: 1200px;
    overflow: hidden;
    background: var(--paper);
  }
  .cover-sheet {
    position: relative;
    width: 1200px;
    height: 1200px;
    background: var(--paper);
  }
  .crop-marks {
    position: absolute;
    inset: 0;
  }
  .cover-art {
    position: absolute;
    left: 32px;
    top: 32px;
    width: 1136px;
    height: 1136px;
    overflow: hidden;
  }
  .stadium-scene {
    position: absolute;
    inset: 0;
    background:
      radial-gradient(ellipse 62% 30% at 50% 48%, var(--glow) 0%, rgba(255,230,150,0.85) 30%, rgba(230,190,90,0.35) 60%, rgba(0,0,0,0) 80%),
      linear-gradient(180deg,
        var(--sky-top) 0%,
        #8f8b6c 14%,
        var(--sky-mid) 30%,
        #e8d796 42%,
        #d9a94e 52%,
        var(--stand-amber) 60%,
        #4d3a24 68%,
        var(--stand-dark) 78%,
        #232a22 86%,
        var(--pitch) 90%,
        var(--pitch-dark) 100%);
  }
  .cover-text {
    position: absolute;
    inset: 0;
    text-align: center;
    font-family: "Reem Kufi", sans-serif;
  }
  .book-title {
    margin: 0;
    position: absolute;
    left: 0;
    right: 0;
    font-weight: 700;
    line-height: 1;
  }
  .book-title .line-one {
    position: absolute;
    left: 0; right: 0;
    top: 100px;
    font-size: 132px;
    color: var(--title-purple);
  }
  .book-title .line-two {
    position: absolute;
    left: 0; right: 0;
    top: 262px;
    font-size: 140px;
    color: var(--title-teal);
  }
  .author {
    position: absolute;
    left: 0; right: 0;
    top: 460px;
    margin: 0;
    font-weight: 500;
    font-size: 58px;
    line-height: 82px;
    color: var(--author-ink);
  }
  .publisher {
    position: absolute;
    left: 0; right: 0;
    top: 1000px;
    display: flex;
    justify-content: center;
    align-items: center;
    gap: 14px;
    font-family: "Reem Kufi", sans-serif;
    font-weight: 700;
    font-size: 40px;
    color: var(--publisher);
  }
  .publisher-mark {
    width: 30px;
    height: 30px;
    background: var(--publisher-mark);
  }
</style>
</head>
<body>
  <div class="cover-sheet">
    <svg class="crop-marks" width="1200" height="1200" viewBox="0 0 1200 1200" aria-hidden="true">
      <g stroke="var(--crop)" stroke-width="1">
        <line x1="58" y1="0" x2="58" y2="26"/>
        <line x1="0" y1="58" x2="26" y2="58"/>
        <line x1="1142" y1="0" x2="1142" y2="26"/>
        <line x1="1174" y1="58" x2="1200" y2="58"/>
        <line x1="58" y1="1174" x2="58" y2="1200"/>
        <line x1="0" y1="1142" x2="26" y2="1142"/>
        <line x1="1142" y1="1174" x2="1142" y2="1200"/>
        <line x1="1174" y1="1142" x2="1200" y2="1142"/>
      </g>
    </svg>

    <div class="cover-art">
      <div class="stadium-scene" role="img" aria-label="Photograph of a floodlit football stadium at sunset: glowing sky, crowded stands and a green pitch"></div>

      <div class="cover-text">
        <h1 class="book-title">
          <span class="line-one">نجوم على</span>
          <span class="line-two">ضفاف الغروب</span>
        </h1>
        <p class="author">المؤلف / الدكتور ناصر<br>بن عيسى المرزوقي</p>
        <div class="publisher">
          <span class="publisher-mark"></span>
          <span class="publisher-name">دار الأفق</span>
        </div>
      </div>
    </div>
  </div>
</body>
</html>
```